Sales presentation introduction for Finance and Tech firms

Our business is two fold - 1) recruitment 2) consultancy. We would like a one or two page template that we can use to send to potential clients. The template will ideally be the same for the recruitment and consultancy side. We need to be able to edit the template to enter text.

I have attached our logo so you can see what we currently use on Corvella.

Sector is financial services and technology. We do not intent to have lots of text but the layout/images/designs to be used should cover some of page in a way that it takes up some space to avoid having to write lot of text.

Open to colour suggestions.

Please look at the attached word doc to see the text I would like for the two presentations.

Happy to answer questions.

Target Market(s)

Directors

Industry/Entity Type

Finance and tech companies

Colors
0094D4
00A9DD
6FCCEA
C7EBF8
E9F6FB

Requirements
Must have
• Editable text

```html
<!DOCTYPE html>
<html lang="en">
<head>
<meta charset="utf-8">
<title>Veritan – Consultancy &amp; Recruitment Brochure Set</title>
<link rel="stylesheet" href="https://fonts.googleapis.com/css2?family=Montserrat:ital,wght@0,300;0,400;0,600;0,700;0,800;1,700;1,800&family=Roboto+Condensed:wght@300;400;700&family=Roboto:ital,wght@0,300;0,400;0,500;0,700;1,700&display=swap">
<style>
:root{
  --navy:#1b355f;
  --navy-deep:#142a4d;
  --royal:#1c5fae;
  --sky:#0094D4;
  --cyan:#00A9DD;
  --light:#6FCCEA;
  --pale:#C7EBF8;
  --mist:#E9F6FB;
  --ink:#232323;
  --grey:#6b6f76;
  --paper:#ffffff;
  --ground:#eef1f5;
}
*{margin:0;padding:0;box-sizing:border-box}
html,body{width:1070px;height:1200px;overflow:hidden;background:var(--ground)}
.canvas{position:relative;width:1070px;height:1200px}
.page{position:absolute;background:var(--paper);overflow:hidden;box-shadow:0 4px 10px rgba(0,0,0,.18);font-family:'Roboto',sans-serif;color:var(--ink)}
.abs{position:absolute}
.photo{position:absolute}
.wordmark{position:absolute;display:flex;align-items:center;gap:6px;font-family:'Roboto',sans-serif;font-weight:400;color:var(--grey)}
.wordmark .mark{background:var(--royal)}
.body-text{font-size:7.3px;line-height:12px;text-align:justify}
.phone-band{position:absolute;left:0;height:30px;display:flex;align-items:center;gap:6px;color:#fff;font-family:'Roboto',sans-serif;font-size:17px;font-weight:400}
.phone-band svg.bg{position:absolute;left:0;top:0;z-index:0}
.phone-band .ico,.phone-band span{position:relative;z-index:1}
.footer{position:absolute;left:0;width:100%;height:26px}
.footer .addr{position:absolute;top:7px;color:#fff;font-family:'Montserrat',sans-serif;font-size:8.6px;font-weight:400}
.footer .web{position:absolute;top:5px;color:#fff;font-family:'Montserrat',sans-serif;font-size:6.2px;line-height:7.4px}
.hero-line{font-family:'Roboto Condensed',sans-serif;color:#fff;text-align:right;font-weight:300;font-size:13px;line-height:17px}
.hero-line b{font-weight:700;font-size:20px;line-height:26px;letter-spacing:.5px}
.hero-line small{font-size:10px}
.band-text{font-family:'Roboto Condensed',sans-serif;color:#fff;font-size:10.4px;line-height:13.5px;font-weight:300}
.service-list{list-style:none}
.service-list li{display:flex;align-items:center;gap:9px;height:13.5px;border-bottom:1px solid #c9cfd8;font-size:8px;color:var(--navy);font-weight:500}
.service-list li svg{flex:none}
h2.section{font-family:'Roboto',sans-serif;font-weight:500;font-size:14px;color:var(--ink)}
h2.caps{font-family:'Montserrat',sans-serif;font-weight:700;font-size:14.5px;color:var(--navy);letter-spacing:.2px}
.specialists{font-family:'Roboto',sans-serif;font-style:italic;font-weight:700;color:var(--sky)}
.tick-list{list-style:none;color:#fff}
.tick-list li{display:flex;gap:6px;align-items:flex-start}
.col-head{font-family:'Roboto',sans-serif;font-weight:700;font-size:13px;color:var(--royal)}
.col-text{font-size:7.3px;line-height:11.4px;text-align:justify;color:var(--ink)}
.hero3{color:#fff;font-family:'Roboto',sans-serif;line-height:1}
.cloud{position:absolute;font-family:'Montserrat',sans-serif;line-height:1;white-space:nowrap}
.c-navy{color:var(--navy)}
.c-white{color:#fff}
.c-dark{color:#1f2a38}
.bi{font-weight:800;font-style:italic}
.lt{font-weight:300}
.rg{font-weight:400}
.p4-text{font-family:'Montserrat',sans-serif;font-size:8.6px;line-height:10.4px;color:var(--royal)}
</style>
</head>
<body>
<div class="canvas">

<section class="page" style="left:46px;top:60px;width:413px;height:535px">
  <div class="photo" role="img" aria-label="Photo of a businessman in a dark suit touching a glowing upward arrow" style="left:0;top:0;width:413px;height:200px;background:linear-gradient(100deg,#2f4f77 0%,#1b2f4c 45%,#0f1c2f 100%)"></div>
  <svg class="abs" style="left:0;top:0" width="413" height="210" viewBox="0 0 413 210">
    <polygon points="0,0 132,0 248,200 0,200" fill="#fff"/>
    <polygon points="132,0 142,0 258,200 248,200" fill="var(--royal)"/>
    <polygon points="40,210 175,95 215,150 250,210" fill="var(--light)"/>
    <polygon points="120,210 185,120 230,175 250,210" fill="var(--sky)"/>
  </svg>
  <div class="wordmark" style="left:28px;top:70px;font-size:23px"><span class="mark" style="width:12px;height:12px"></span>VERITAN</div>
  <div class="hero-line abs" style="left:200px;top:68px;width:119px">VERITAN WILL<br>ENSURE <small>YOU ARE</small><br>PREPARED <small>FOR</small><br><b>GROWTH.</b></div>
  <svg class="abs" style="left:0;top:151px" width="350" height="40"><polygon points="0,0 335,0 350,40 0,40" fill="rgba(40,58,98,.85)"/></svg>
  <div class="band-text abs" style="left:25px;top:158px">A partner who brings new and innovative ideas to the table,<br>through extensive industry experience and knowledge.</div>
  <div class="abs" style="left:0;top:201px;width:413px;height:7px;background:var(--light)"></div>

  <h2 class="section abs" style="left:23px;top:221px">Veritan Consultancy</h2>
  <div class="body-text abs" style="left:24px;top:241px;width:372px">Veritan E2E is a bespoke consultancy firm that specialises in buy side investment. Through an industry based consultative approach we assist our clients in preparing for, and facilitating, long term growth. Working closely with our clients we combine innovative thinking and breakthrough technologies to accelerate progress and, together, achieve enduring results.<br>Experienced in successfully delivering change for global organisations as well as assisting smaller firms during their growth phase. Veritan will work with you create a workable model and ensure successful delivery of the project.</div>

  <ul class="service-list abs" style="left:28px;top:335px;width:178px">
    <li><svg width="9" height="8"><path d="M1 4l2.5 2.5L8 1.5" stroke="var(--sky)" stroke-width="1.6" fill="none"/></svg>Order Management and Trading</li>
    <li><svg width="9" height="8"><path d="M1 4l2.5 2.5L8 1.5" stroke="var(--sky)" stroke-width="1.6" fill="none"/></svg>Investment and Research</li>
    <li><svg width="9" height="8"><path d="M1 4l2.5 2.5L8 1.5" stroke="var(--sky)" stroke-width="1.6" fill="none"/></svg>Static, Pricing and Benchmark Data</li>
    <li><svg width="9" height="8"><path d="M1 4l2.5 2.5L8 1.5" stroke="var(--sky)" stroke-width="1.6" fill="none"/></svg>CRM/ Onboarding</li>
    <li><svg width="9" height="8"><path d="M1 4l2.5 2.5L8 1.5" stroke="var(--sky)" stroke-width="1.6" fill="none"/></svg>Performance, Risk and Attribution</li>
    <li><svg width="9" height="8"><path d="M1 4l2.5 2.5L8 1.5" stroke="var(--sky)" stroke-width="1.6" fill="none"/></svg>Client and Regulatory Reporting</li>
    <li><svg width="9" height="8"><path d="M1 4l2.5 2.5L8 1.5" stroke="var(--sky)" stroke-width="1.6" fill="none"/></svg>Compliance</li>
    <li><svg width="9" height="8"><path d="M1 4l2.5 2.5L8 1.5" stroke="var(--sky)" stroke-width="1.6" fill="none"/></svg>Finance and Accounting</li>
    <li><svg width="9" height="8"><path d="M1 4l2.5 2.5L8 1.5" stroke="var(--sky)" stroke-width="1.6" fill="none"/></svg>Middle and Back Office</li>
  </ul>
  <div class="photo" role="img" aria-label="Photo of colleagues reviewing charts on a laptop and printed reports" style="left:207px;top:337px;width:184px;height:130px;background:linear-gradient(135deg,#6d6a60 0%,#b9b6ae 40%,#e3e4e6 70%,#9aa4b0 100%)"></div>

  <div class="phone-band" style="top:467px;width:168px;padding-left:30px">
    <svg class="bg" width="168" height="30"><polygon points="0,0 168,0 155,30 0,30" fill="var(--navy)"/></svg>
    <svg class="ico" width="12" height="12" viewBox="0 0 24 24"><path d="M6 2l4 5-2 3c1 3 3 5 6 6l3-2 5 4-3 4C10 22 2 14 2 5z" fill="none" stroke="#fff" stroke-width="1.8"/></svg>
    <span>555 014 2880</span>
  </div>
  <div class="footer" style="top:499px">
    <svg width="413" height="26"><polygon points="0,0 232,0 245,26 0,26" fill="var(--navy)"/><polygon points="228,0 242,0 255,26 241,26" fill="#b7c3dc"/><polygon points="245,0 262,0 275,26 258,26" fill="#8fa3c9"/><polygon points="268,0 413,0 413,26 281,26" fill="var(--royal)"/></svg>
    <span class="addr" style="left:23px">18 Harbor Row, Stamford, CT 06901</span>
    <span class="web" style="left:295px">info@veritan-example.com<br>www.veritan-example.com</span>
  </div>
</section>

<section class="page" style="left:584px;top:64px;width:411px;height:532px">
  <div class="photo" role="img" aria-label="Photo of a businessman offering a handshake with colleagues in a bright office behind" style="left:0;top:0;width:411px;height:200px;background:linear-gradient(100deg,#cfd6de 0%,#e7e9ec 45%,#8fb7de 75%,#3f6fa3 100%)"></div>
  <svg class="abs" style="left:0;top:0" width="411" height="210" viewBox="0 0 411 210">
    <polygon points="0,0 135,0 250,200 0,200" fill="#fff"/>
    <polygon points="135,0 146,0 261,200 250,200" fill="var(--royal)"/>
    <polygon points="50,210 175,95 220,150 260,210" fill="var(--light)"/>
    <polygon points="125,210 185,120 235,175 260,210" fill="var(--sky)"/>
  </svg>
  <div class="wordmark" style="left:28px;top:86px;font-size:23px"><span class="mark" style="width:12px;height:12px"></span>VERITAN</div>
  <div class="abs" style="left:40px;top:108px;font-family:'Roboto Condensed',sans-serif;font-weight:700;font-size:11px;color:var(--royal)">RECRUITMENT</div>
  <svg class="abs" style="left:0;top:142px" width="360" height="57"><polygon points="0,0 335,0 360,57 0,57" fill="rgba(30,52,96,.92)"/></svg>
  <div class="abs" style="left:23px;top:148px;font-family:'Roboto Condensed',sans-serif;color:#fff;font-size:9.6px;line-height:12px;font-weight:700">A partner who brings new and innovative ideas to the table,<br>through extensive industry experience and knowledge.</div>
  <div class="abs" style="left:23px;top:173px;font-family:'Roboto Condensed',sans-serif;color:#fff;font-size:13px;font-weight:700">Veritan will ensure you are prepared for growth.</div>
  <div class="abs" style="left:0;top:201px;width:411px;height:7px;background:var(--light)"></div>

  <h2 class="caps abs" style="left:23px;top:220px">VERITAN RECRUITMENT</h2>
  <div class="body-text abs" style="left:24px;top:240px;width:368px;line-height:9.8px">Veritan is more than an ordinary recruitment service. Our experts work with clients to develop a HR strategy that maps current, and impending, organisational needs; using research to effectively benchmark. We are developing various talent communities that provide effective, and timely, recruitment solutions for our clients.</div>
  <div class="specialists abs" style="left:23px;top:281px;font-size:12.5px">Specialists in:</div>
  <div class="specialists abs" style="left:23px;top:296px;font-size:7.4px;line-height:9.6px">Asset Management recruitment with a specialisation in<br>I.T, Operations, Regulation and Change Management.</div>
  <div class="body-text abs" style="left:23px;top:317px;width:187px;line-height:9.8px">Veritan acts as an extension of your HR function, providing an end-to-end permanent and contingent talent acquisition solution, taking full accountability and ownership for the entire recruitment process, which includes:</div>
  <div class="abs" style="left:224px;top:288px;width:168px;height:77px;background:var(--navy);border-radius:7px"></div>
  <ul class="tick-list abs" style="left:236px;top:297px;font-size:7.6px;font-weight:500;line-height:12.1px">
    <li><svg width="8" height="10"><path d="M1 5l2 2.5L7 2" stroke="var(--light)" stroke-width="1.5" fill="none"/></svg>Workforce Planning</li>
    <li><svg width="8" height="10"><path d="M1 5l2 2.5L7 2" stroke="var(--light)" stroke-width="1.5" fill="none"/></svg>Strategic Sourcing</li>
    <li><svg width="8" height="10"><path d="M1 5l2 2.5L7 2" stroke="var(--light)" stroke-width="1.5" fill="none"/></svg>Talent Engagement</li>
    <li><svg width="8" height="10"><path d="M1 5l2 2.5L7 2" stroke="var(--light)" stroke-width="1.5" fill="none"/></svg>Candidate Management</li>
    <li><svg width="8" height="10"><path d="M1 5l2 2.5L7 2" stroke="var(--light)" stroke-width="1.5" fill="none"/></svg>Weekly vacancy updates</li>
  </ul>
  <div class="abs" style="left:22px;top:373px;width:369px;height:1px;background:#c6ccd4"></div>
  <div class="body-text abs" style="left:22px;top:390px;width:188px;line-height:9.8px">We recognise that hiring can be a lengthy process, therefore we partner with you to ensure you only interview top quantile candidates, cutting out multiple meetings with multiple candidates. Giving hiring managers time back in their diaries to do their day jobs and reducing the time to hire.</div>
  <div class="abs" style="left:225px;top:383px;width:167px;height:92px;background:#3f7ec9;border-radius:7px"></div>
  <div class="abs" style="left:237px;top:389px;color:#fff;font-size:8.2px">This is achieved by:</div>
  <ul class="tick-list abs" style="left:237px;top:403px;width:150px;font-size:6.2px;line-height:7.8px">
    <li style="margin-bottom:6px"><svg width="8" height="8" style="flex:none"><path d="M1 4l2 2.5L7 1" stroke="var(--navy)" stroke-width="1.5" fill="none"/></svg><span>Understanding the roles, and partnering with you to build meaningful job descriptions</span></li>
    <li style="margin-bottom:5px"><svg width="8" height="8" style="flex:none"><path d="M1 4l2 2.5L7 1" stroke="var(--navy)" stroke-width="1.5" fill="none"/></svg><span>Candidates are fully screened and interviewed prior to presentation to you</span></li>
    <li style="margin-bottom:3px"><svg width="8" height="8" style="flex:none"><path d="M1 4l2 2.5L7 1" stroke="var(--navy)" stroke-width="1.5" fill="none"/></svg><span>Qualified shortlist of top 3 candidates</span></li>
    <li><svg width="8" height="8" style="flex:none"><path d="M1 4l2 2.5L7 1" stroke="var(--navy)" stroke-width="1.5" fill="none"/></svg><span>Support with interviews and we ensure the candidate has a positive experience</span></li>
  </ul>

  <div class="phone-band" style="top:464px;width:168px;padding-left:30px">
    <svg class="bg" width="168" height="30"><polygon points="0,0 168,0 155,30 0,30" fill="var(--navy)"/></svg>
    <svg class="ico" width="12" height="12" viewBox="0 0 24 24"><path d="M6 2l4 5-2 3c1 3 3 5 6 6l3-2 5 4-3 4C10 22 2 14 2 5z" fill="none" stroke="#fff" stroke-width="1.8"/></svg>
    <span>555 014 2880</span>
  </div>
  <div class="footer" style="top:495px">
    <svg width="411" height="26"><polygon points="0,0 232,0 245,26 0,26" fill="var(--navy)"/><polygon points="228,0 242,0 255,26 241,26" fill="#b7c3dc"/><polygon points="245,0 262,0 275,26 258,26" fill="#8fa3c9"/><polygon points="268,0 411,0 411,26 281,26" fill="var(--royal)"/></svg>
    <span class="addr" style="left:23px">18 Harbor Row, Stamford, CT 06901</span>
    <span class="web" style="left:293px">info@veritan-example.com<br>www.veritan-example.com</span>
  </div>
</section>

<section class="page" style="left:66px;top:639px;width:390px;height:504px">
  <div class="photo" role="img" aria-label="Photo of a businessman drawing a rising line on a glowing financial data screen" style="left:0;top:0;width:390px;height:180px;background:linear-gradient(110deg,#6fb3d6 0%,#3f8fbd 35%,#1e5c8a 65%,#10304f 100%)"></div>
  <div class="hero3 abs" style="left:18px;top:32px;font-size:25px;font-weight:300">Business Strategy</div>
  <div class="hero3 abs" style="left:43px;top:62px;font-size:24px;font-weight:700;letter-spacing:.3px">MANAGEMENT</div>
  <div class="hero3 abs" style="left:25px;top:90px;font-size:14.5px;font-weight:300">IT TRANSFORMATION</div>
  <div class="hero3 abs" style="left:40px;top:107px;font-size:13px;font-weight:700">Organisational structure</div>

  <h3 class="col-head abs" style="left:18px;top:197px">Business Strategy</h3>
  <p class="col-text abs" style="left:18px;top:220px;width:155px">Veritan will help you create a business strategy tailored to your requirements. Ensuring each business process is defined and taken into account allows for a successful design. Creating and implementing an operating model that takes into account budget, resources, culture and your company's vision.</p>
  <h3 class="col-head abs" style="left:190px;top:196px">Change management</h3>
  <p class="col-text abs" style="left:190px;top:219px;width:183px">Veritan works with clients to deliver bespoke change initiatives. Rigorous business analysis and risk management allows for successful change initiatives. We work with you throughout the complete process, to ensure that delivery is based on value. Transition phases are challenging aspects of change initiatives which is why our team manage all transitions and the risk they carry.</p>
  <h3 class="col-head abs" style="left:18px;top:317px">IT transformation</h3>
  <p class="col-text abs" style="left:18px;top:340px;width:155px">Veritan is widely experienced in a range of technologies. We help with the implementation of software provider or design and develop bespoke services. Covering front to back office the team specialises in full project lifecycle from feasibility through to implementation.</p>
  <h3 class="col-head abs" style="left:190px;top:316px">Organisational structure</h3>
  <p class="col-text abs" style="left:190px;top:339px;width:183px">Veritan works with clients to improve resource capability and strategic partnerships. Acting as an extension of the HR function, we analyse business processes and ensure that our clients have the ability to manage changing workforce demands.</p>

  <div class="wordmark" style="left:22px;top:444px;font-size:17px"><span class="mark" style="width:10px;height:10px"></span>VERITAN</div>
  <div class="phone-band" style="top:441px;left:238px;width:152px;padding-left:28px;font-size:16px">
    <svg class="bg" width="152" height="30"><polygon points="0,0 152,0 152,30 13,30" fill="var(--navy)"/></svg>
    <svg class="ico" width="12" height="12" viewBox="0 0 24 24"><path d="M6 2l4 5-2 3c1 3 3 5 6 6l3-2 5 4-3 4C10 22 2 14 2 5z" fill="none" stroke="#fff" stroke-width="1.8"/></svg>
    <span>555 014 2880</span>
  </div>
  <div class="footer" style="top:471px;height:22px">
    <svg width="390" height="22"><polygon points="0,0 216,0 228,22 0,22" fill="var(--navy)"/><polygon points="212,0 226,0 238,22 224,22" fill="#b7c3dc"/><polygon points="229,0 246,0 258,22 241,22" fill="#8fa3c9"/><polygon points="240,0 390,0 390,22 252,22" fill="var(--royal)"/></svg>
    <span class="addr" style="left:22px;top:6px">18 Harbor Row, Stamford, CT 06901</span>
    <span class="web" style="left:279px;top:3px">info@veritan-example.com<br>www.veritan-example.com</span>
  </div>
</section>

<section class="page" style="left:589px;top:624px;width:402px;height:519px">
  <div class="photo" role="img" aria-label="Photo of a businessman's open hand holding floating candidate profile pins" style="left:0;top:0;width:402px;height:342px;background:linear-gradient(120deg,#c5d8e4 0%,#8fb0c6 35%,#5a8099 65%,#2d4b63 100%)"></div>
  <div class="cloud c-navy" style="left:36px;top:25px;font-size:19px;font-weight:700">FIXED INCOME</div>
  <div class="cloud c-white lt" style="left:36px;top:46px;font-size:24px">EQUITY</div>
  <div class="cloud c-dark bi" style="left:133px;top:55px;font-size:13px">Settlement</div>
  <div class="cloud c-navy" style="left:36px;top:73px;font-size:17px;font-weight:800">Trading Platforms</div>
  <div class="cloud c-white lt" style="left:36px;top:95px;font-size:31px">MIS</div>
  <div class="cloud c-dark rg" style="left:109px;top:95px;font-size:14px">Lumora</div>
  <div class="cloud c-dark rg" style="left:109px;top:113px;font-size:14px">stack</div>
  <div class="cloud c-navy bi" style="left:36px;top:130px;font-size:12.5px">Workflow Management</div>
  <div class="cloud c-white bi" style="left:36px;top:145px;font-size:23px">SQL</div>
  <div class="cloud c-navy" style="left:99px;top:152px;font-size:11px;font-weight:700;letter-spacing:4px">Kestrel</div>
  <div class="cloud c-navy rg" style="left:79px;top:164px;font-size:20px">XML</div>
  <div class="cloud c-white bi" style="left:133px;top:166px;font-size:14px">FIX/RELAY</div>
  <div class="cloud c-white bi" style="left:61px;top:185px;font-size:20px">BUSINESS</div>
  <div class="cloud c-white" style="left:95px;top:206px;font-size:11px;font-weight:700;letter-spacing:4px">Intelligence</div>
  <div class="cloud c-navy rg" style="left:36px;top:222px;font-size:15px">PRICING AND ANALYTICS</div>
  <div class="cloud c-white bi" style="left:36px;top:245px;font-size:9px;line-height:11px">COLLATERAL<br>MANAGEMENT</div>
  <div class="cloud c-white rg" style="left:119px;top:244px;font-size:22px">Connectivity</div>
  <div class="cloud c-navy rg" style="left:62px;top:269px;font-size:20px">REFERENCE DATA</div>
  <div class="cloud c-white rg" style="left:36px;top:298px;font-size:11px">RISK AND ATTRIBUTION</div>
  <div class="cloud c-white bi" style="left:187px;top:292px;font-size:21px">Batch processing</div>

  <h2 class="caps abs" style="left:23px;top:361px;font-size:15px">VERITAN RECRUITMENT</h2>
  <p class="p4-text abs" style="left:24px;top:384px;width:300px">partners with principal business consultants from Veritan consultancy to ensure candidates are properly screened before presenting to our clients.</p>
  <p class="p4-text abs" style="left:24px;top:426px;width:370px">This allows for our clients to focus on only interviewing the best on the market.</p>

  <div class="phone-band" style="top:453px;width:163px;padding-left:30px">
    <svg class="bg" width="163" height="30"><polygon points="0,0 163,0 150,30 0,30" fill="var(--navy)"/></svg>
    <svg class="ico" width="12" height="12" viewBox="0 0 24 24"><path d="M6 2l4 5-2 3c1 3 3 5 6 6l3-2 5 4-3 4C10 22 2 14 2 5z" fill="none" stroke="#fff" stroke-width="1.8"/></svg>
    <span>555 014 2880</span>
  </div>
  <div class="footer" style="top:483px;height:24px">
    <svg width="402" height="24"><polygon points="0,0 220,0 232,24 0,24" fill="var(--navy)"/><polygon points="216,0 230,0 242,24 228,24" fill="#b7c3dc"/><polygon points="233,0 250,0 262,24 245,24" fill="#8fa3c9"/><polygon points="246,0 402,0 402,24 258,24" fill="var(--royal)"/></svg>
    <span class="addr" style="left:22px;top:6px">18 Harbor Row, Stamford, CT 06901</span>
    <span class="web" style="left:287px;top:4px">info@veritan-example.com<br>www.veritan-example.com</span>
  </div>
</section>

</div>
</body>
</html>
```